Business Card for a New Zealand IT Startup

I need a business card for VELTA Holdings. We are a young startup based in New Zealand working in internet marketing and web development. The design should have some element connected to New Zealand, such as wave, koru or silver fern, just don't use a kiwi bird.

```html
<!DOCTYPE html>
<html lang="en">
<head>
<meta charset="utf-8">
<title>VELTA Holdings – Business Card</title>
<link href="https://fonts.googleapis.com/css2?family=Montserrat:wght@700&family=Open+Sans:wght@400;600;700&display=swap" rel="stylesheet">
<style>
  :root {
    --backdrop: #dcdcdc;
    --card: #ffffff;
    --brand-blue: #1769b3;
    --brand-orange: #e0561f;
    --band-mid: #7a5a5e;
    --band-end: #2f6aa8;
    --ink: #333333;
  }
  * { box-sizing: border-box; margin: 0; padding: 0; }
  html, body { width: 1200px; height: 852px; overflow: hidden; }
  body {
    background: var(--backdrop);
    font-family: "Open Sans", Arial, sans-serif;
    position: relative;
  }
  .card {
    position: absolute;
    width: 500px;
    height: 290px;
    background: var(--card);
    border-radius: 22px;
    overflow: hidden;
    box-shadow: 0 4px 14px rgba(0,0,0,0.18);
  }
  .card--front { left: 60px; top: 281px; }
  .card--back { left: 640px; top: 281px; }

  .brand-name {
    font-family: "Montserrat", Arial, sans-serif;
    font-weight: 700;
    color: var(--brand-blue);
    white-space: nowrap;
  }

  /* Front */
  .front-brand {
    position: absolute;
    top: 96px; left: 0; right: 0;
    text-align: center;
    font-size: 44px;
    letter-spacing: 1px;
  }
  .front-web {
    position: absolute;
    top: 226px; left: 0; right: 0;
    display: flex; align-items: center; justify-content: center; gap: 12px;
    font-size: 13px; font-weight: 600; color: var(--ink);
  }
  .front-web .rule { width: 60px; height: 2px; background: var(--brand-blue); }
  .front-web .accent { color: var(--brand-blue); }
  .front-web .accent-2 { color: var(--brand-orange); }

  /* Back */
  .back-art { position: absolute; inset: 0; }
  .back-brand {
    position: absolute;
    top: 72px; left: 26px;
    font-size: 26px;
  }
  .person {
    position: absolute;
    left: 26px; top: 136px;
    color: #fff;
  }
  .person__name { font-size: 20px; font-weight: 700; line-height: 1.1; }
  .person__role { font-size: 11px; margin-bottom: 8px; }
  .contact { list-style: none; font-size: 12px; }
  .contact li { display: flex; align-items: center; gap: 10px; height: 18px; }
  .contact svg { width: 11px; height: 11px; fill: #fff; flex: none; }
  .address {
    position: absolute;
    left: 26px; bottom: 14px;
    font-size: 12px; color: var(--ink);
  }
</style>
</head>
<body>

  <section class="card card--front" aria-label="Business card front">
    <div class="brand-name front-brand">VELTA Holdings</div>
    <div class="front-web">
      <span class="rule"></span>
      <span>www.<span class="accent">velta</span><span class="accent-2">holdings</span>.com</span>
      <span class="rule"></span>
    </div>
  </section>

  <section class="card card--back" aria-label="Business card back">
    <svg class="back-art" viewBox="0 0 500 290" width="500" height="290" aria-hidden="true">
      <defs>
        <linearGradient id="bandFade" x1="0" y1="1" x2="1" y2="0">
          <stop offset="0" stop-color="#e0561f"/>
          <stop offset="0.55" stop-color="#7a5a5e"/>
          <stop offset="1" stop-color="#2f6aa8"/>
        </linearGradient>
      </defs>
      <rect x="0" y="115" width="500" height="135" fill="url(#bandFade)"/>
      <rect x="430" y="28" width="70" height="130" fill="#1769b3"/>
      <rect x="340" y="28" width="90" height="87" fill="#ffffff"/>
      <circle cx="380" cy="105" r="72" fill="#ffffff"/>
      <circle cx="380" cy="105" r="62" fill="#3d6a9e"/>
    </svg>

    <div class="brand-name back-brand">VELTA Holdings</div>

    <div class="person">
      <div class="person__name">John Doe Smith</div>
      <div class="person__role">Managing Director</div>
      <ul class="contact">
        <li><svg viewBox="0 0 24 24"><path d="M6.6 10.8a15 15 0 0 0 6.6 6.6l2.2-2.2c.3-.3.7-.4 1-.2 1.1.4 2.3.6 3.6.6.6 0 1 .4 1 1V20c0 .6-.4 1-1 1A17 17 0 0 1 3 4c0-.6.4-1 1-1h3.5c.6 0 1 .4 1 1 0 1.3.2 2.5.6 3.6.1.3 0 .7-.2 1z"/></svg>555-0193-472</li>
        <li><svg viewBox="0 0 24 24"><path d="M2 5h20v14H2zM3.5 6.5 12 13l8.5-6.5"/></svg>velta@veltaholdings.com</li>
        <li><svg viewBox="0 0 24 24"><path d="M12 2a10 10 0 1 0 0 20 10 10 0 0 0 0-20zm0 2c1 1.4 1.8 3.2 2 5h-4c.2-1.8 1-3.6 2-5zM4.3 13h3.8c.1 1.8.6 3.5 1.3 5A8 8 0 0 1 4.3 13zm0-2a8 8 0 0 1 5.1-6c-.7 1.5-1.2 3.2-1.3 6zm7.7 9c-1-1.4-1.8-3.2-2-5h4c-.2 1.8-1 3.6-2 5zm2.6-1c.7-1.5 1.2-3.2 1.3-5h3.8a8 8 0 0 1-5.1 5zm1.3-7c-.1-2.8-.6-4.5-1.3-6a8 8 0 0 1 5.1 6z"/></svg>www.veltaholdings.com</li>
      </ul>
    </div>

    <div class="address">48 Kowhai Lane, Newmarket, Auckland, NZ 1023</div>
  </section>

</body>
</html>
```